New Business Card for Software Company

We are looking at rebranding a 10 year old company that specializes in PDF and DWF solutions for Architects and Engineers. We will attach the new company logo that we are going with so you can work with that and complimentary colors.
The sample information we would like on the business card is:
Gerald Pinfold
Vice President
4738 W. Harrowgate Lane. STE 305
PMB#417
Mesa, AZ 85374
866-392-5074 US Toll Free
123-456-3190 Cell
gpinfold@plavorix.com
The old tag line that we had on the business cars was.
Providing Industrial Strength PDF and DWF Solutions to the Global CAD Marketplace.
If you have an idea for a better tag line we are open to that also.
Updates
We would like to thank all of the Designers for their wonderful work. We apologize that we will not have the time to provide feedback to everyone. There is just so many innovative and professional designs that you have all created making our decision even harder.
Target Market(s)
Architects and Engineers
Industry/Entity Type
Business
Look and feel

```html
<!DOCTYPE html>
<html lang="en">
<head>
<meta charset="utf-8">
<title>Plavorix Business Card</title>
<link rel="stylesheet" href="https://fonts.googleapis.com/css2?family=Arimo:wght@400;700&family=Open+Sans:wght@400&display=swap">
<style>
  :root {
    --page: #e9eaee;
    --card-white: #ffffff;
    --slate: #626262;
    --slate-dark: #555555;
    --brand-orange: #f26522;
    --brand-red: #c8242e;
    --brand-amber: #f7941d;
    --text-light: #ffffff;
  }
  * { margin: 0; padding: 0; box-sizing: border-box; }
  html, body { width: 1200px; height: 987px; overflow: hidden; }
  body { background: var(--page); position: relative; font-family: "Arimo", Arial, sans-serif; }

  .card {
    position: absolute;
    width: 560px;
    height: 320px;
    border-radius: 18px;
    overflow: hidden;
    box-shadow: 0 10px 28px rgba(0,0,0,0.18);
  }

  /* Front */
  .card-front { left: 60px; top: 560px; background: var(--card-white); }
  .front-brand {
    height: 118px;
    display: flex;
    align-items: center;
    padding-left: 42px;
    gap: 16px;
  }
  .brand-dot {
    width: 62px; height: 62px; border-radius: 50%;
    background: var(--brand-orange);
    flex: none;
  }
  .brand-name {
    font-family: "Arimo", Arial, sans-serif;
    font-weight: 700;
    font-size: 68px;
    letter-spacing: -2px;
    color: var(--slate);
    line-height: 1;
  }
  .front-contact {
    height: 152px;
    background: var(--slate);
    color: var(--text-light);
    display: flex;
    align-items: center;
    font-size: 17px;
    line-height: 1.3;
  }
  .address { width: 250px; text-align: right; padding-right: 18px; }
  .divider { width: 1px; height: 92px; background: rgba(255,255,255,0.55); }
  .contact-list { list-style: none; padding-left: 16px; }
  .contact-list li { display: flex; align-items: center; gap: 8px; }
  .contact-list svg { width: 14px; height: 14px; flex: none; fill: var(--text-light); }
  .name-band {
    height: 50px;
    background: linear-gradient(90deg, var(--brand-red), var(--brand-orange) 45%, var(--brand-amber));
    color: var(--text-light);
    display: flex;
    align-items: center;
    padding-left: 26px;
    font-size: 22px;
  }
  .person-name { font-weight: 700; }
  .person-title { font-weight: 400; margin-left: 6px; font-size: 20px; }

  /* Back */
  .card-back {
    left: 590px; top: 110px;
    background: var(--slate);
    display: flex;
    flex-direction: column;
    align-items: center;
    justify-content: center;
    gap: 26px;
  }
  .back-brand { display: flex; align-items: center; gap: 16px; }
  .back-brand .brand-name { color: var(--text-light); font-size: 56px; }
  .back-brand .brand-dot { width: 54px; height: 54px; }
  .tagline {
    font-family: "Open Sans", Arial, sans-serif;
    color: var(--text-light);
    font-size: 18px;
    text-align: center;
    line-height: 1.35;
  }
</style>
</head>
<body>

<section class="card card-back">
  <div class="back-brand">
    <span class="brand-dot"></span>
    <span class="brand-name">plavorix</span>
  </div>
  <p class="tagline">Providing Industrial Strength PDF and DWF Solutions<br>to the Global CAD Marketplace</p>
</section>

<section class="card card-front">
  <div class="front-brand">
    <span class="brand-dot"></span>
    <span class="brand-name">plavorix</span>
  </div>
  <div class="front-contact">
    <address class="address" style="font-style:normal">
      4738 W. Harrowgate Lane<br>
      STE 305<br>
      PMB#417, Mesa, AZ 85374
    </address>
    <span class="divider"></span>
    <ul class="contact-list">
      <li>
        <svg viewBox="0 0 24 24" aria-hidden="true"><path d="M6.6 10.8a15.1 15.1 0 0 0 6.6 6.6l2.2-2.2a1 1 0 0 1 1-.25 11.4 11.4 0 0 0 3.6.57 1 1 0 0 1 1 1V20a1 1 0 0 1-1 1A17 17 0 0 1 3 4a1 1 0 0 1 1-1h3.5a1 1 0 0 1 1 1c0 1.25.2 2.45.57 3.57a1 1 0 0 1-.25 1z"/></svg>
        866-392-5074(US) TF
      </li>
      <li>
        <svg viewBox="0 0 24 24" aria-hidden="true"><path d="M7 1h10a2 2 0 0 1 2 2v18a2 2 0 0 1-2 2H7a2 2 0 0 1-2-2V3a2 2 0 0 1 2-2zm0 3v13h10V4zm5 15a1.2 1.2 0 1 0 0 2.4 1.2 1.2 0 0 0 0-2.4z"/></svg>
        123-456-3190
      </li>
      <li>
        <svg viewBox="0 0 24 24" aria-hidden="true"><path d="M2 5h20v14H2zm2 2v.5l8 5 8-5V7zm0 2.8V17h16V9.8l-8 5z"/></svg>
        gpinfold@plavorix.com
      </li>
    </ul>
  </div>
  <div class="name-band">
    <span class="person-name">Gerald Pinfold,</span>
    <span class="person-title">Vice President</span>
  </div>
</section>

</body>
</html>
```